Business Card Design Project

This is the first time we use our new logo. We need a business card that we can use both on our institutional corporate relationships and also that works for our staff that deals with consumers directly.

VELUNDA is a new company dedicated to empower consumers and to provide them with the best choices for specialized health care using the latest telemedicine technology (medicine at a distance via videoconference).

We want to print this cards in high quality materials and process. We will like designs that allow us to use UV spot varnish and other techniques that will differentiate us.

We are including Two different versions of Color logos. In addition we are including white over black background logos. Those can be used replacing the black for a color.

Please note this is the first time we will be creating any corporate materials with our new logo and colors.

Target Market(s)

34+ consumers of medium high and high socioeconomic levels.

Industry/Entity Type

Health

Requirements
Must have
• Our logo on its original colors
Should not have
• Any other graphical element or design that is not our logo

```html
<!DOCTYPE html>
<html lang="en">
<head>
<meta charset="utf-8">
<title>VELUNDA business card</title>
<link href="https://fonts.googleapis.com/css2?family=Jost:wght@600&family=Open+Sans:wght@400&family=Roboto+Condensed:wght@400;700&display=swap" rel="stylesheet">
<style>
  :root {
    --stage: #e4e4e6;
    --brand-blue: #1b75bc;
    --brand-navy: #1d4f7a;
    --brand-teal: #17a398;
    --paper: #ffffff;
    --ink: #3a3a3a;
    --ink-soft: #4a4a4a;
    --icon: #1b6fb5;
  }
  * { margin: 0; padding: 0; box-sizing: border-box; }
  html, body {
    width: 1200px;
    height: 1027px;
    overflow: hidden;
    background: var(--stage);
  }
  .canvas {
    position: relative;
    width: 1200px;
    height: 1027px;
  }
  .card {
    position: absolute;
    top: 126px;
    width: 352px;
    height: 616px;
    box-shadow: 0 2px 6px rgba(0,0,0,0.12);
  }
  .card--front { left: 234px; background: var(--brand-blue); }
  .card--back  { left: 613px; background: var(--paper); }

  .brand {
    position: absolute;
    left: 50px;
    top: 100px;
    display: flex;
    align-items: center;
    gap: 16px;
  }
  .brand__dot {
    width: 52px;
    height: 52px;
    border-radius: 50%;
  }
  .brand__name {
    font-family: "Jost", sans-serif;
    font-weight: 600;
    font-size: 37px;
    letter-spacing: 2px;
    line-height: 1;
  }
  .card--front .brand__dot { background: var(--paper); }
  .card--front .brand__name { color: var(--paper); }
  .card--back .brand__dot { background: var(--brand-teal); }
  .card--back .brand__name { color: var(--brand-navy); }

  .person {
    position: absolute;
    left: 67px;
    top: 326px;
  }
  .person__name {
    font-family: "Roboto Condensed", sans-serif;
    font-weight: 400;
    font-size: 18px;
    color: var(--ink);
    word-spacing: 4px;
  }
  .person__role {
    font-family: "Roboto Condensed", sans-serif;
    font-weight: 700;
    font-size: 13px;
    color: var(--brand-navy);
    margin-top: 3px;
  }
  .contacts {
    position: absolute;
    left: 58px;
    top: 414px;
    list-style: none;
  }
  .contacts__item {
    display: flex;
    align-items: center;
    height: 20.5px;
    font-family: "Open Sans", sans-serif;
    font-size: 15px;
    color: var(--ink-soft);
  }
  .contacts__icon {
    width: 16px;
    height: 16px;
    margin-right: 12px;
    fill: var(--icon);
  }
</style>
</head>
<body>
<main class="canvas">
  <section class="card card--front">
    <div class="brand">
      <span class="brand__dot"></span>
      <span class="brand__name">VELUNDA</span>
    </div>
  </section>

  <section class="card card--back">
    <div class="brand">
      <span class="brand__dot"></span>
      <span class="brand__name">VELUNDA</span>
    </div>

    <div class="person">
      <p class="person__name">Maren Solt</p>
      <p class="person__role">CEO</p>
    </div>

    <ul class="contacts">
      <li class="contacts__item">
        <svg class="contacts__icon" viewBox="0 0 16 16" aria-hidden="true"><rect x="4" y="1" width="8" height="14" rx="1.5"/><rect x="5.5" y="3" width="5" height="8" fill="#fff"/><circle cx="8" cy="13" r="0.9" fill="#fff"/></svg>
        (000) 000-0000
      </li>
      <li class="contacts__item">
        <svg class="contacts__icon" viewBox="0 0 16 16" aria-hidden="true"><rect x="4" y="1" width="8" height="4"/><rect x="1" y="6" width="14" height="6" rx="1"/><rect x="4" y="10" width="8" height="5"/></svg>
        (000) 000-0000
      </li>
      <li class="contacts__item">
        <svg class="contacts__icon" viewBox="0 0 16 16" aria-hidden="true"><rect x="1" y="3" width="14" height="10" rx="1"/><path d="M1.5 3.8 8 9l6.5-5.2" fill="none" stroke="#fff" stroke-width="1.3"/></svg>
        hello@velunda.com
      </li>
      <li class="contacts__item">
        <svg class="contacts__icon" viewBox="0 0 16 16" aria-hidden="true"><circle cx="8" cy="8" r="7"/><g fill="none" stroke="#fff" stroke-width="1"><ellipse cx="8" cy="8" rx="3" ry="7"/><path d="M1 8h14M2.2 4.5h11.6M2.2 11.5h11.6"/></g></svg>
        www.velunda.com
      </li>
    </ul>
  </section>
</main>
</body>
</html>
```